FinTech company looking to revamp and expand client-facing interface for our financial models

Pellworth Engines currently has a very simple website that allows clients to interact with our financial models. We are looking to completely redesign the current site and add several extra pages to provide extra functionality. We want the design to have a modern, slick feel, that will work on both a desktop or a tablet. It should be straightforward for clients to move between different pages at any time, and clear from the layout how to interact with the more advanced features. We have included screenshots of existing pages in the attached design brief, as well as sketches of the functionality required by the new pages, but can't provide a direct link to the current site.
Target Market(s)
Professional investors that will be paying to access the interface
Industry/Entity Type
Finance
Number of Pages Required
4 page
Colors
Designer to choose colors to be used in the design.
Look and feel
Each slider illustrates characteristics of the customer's brand and the style your logo design should communicate.

```html
<!DOCTYPE html>
<html lang="en">
<head>
<meta charset="utf-8">
<title>Pellworth Engines – Models</title>
<link href="https://fonts.googleapis.com/css2?family=Montserrat:wght@500;600;700&family=Roboto+Condensed:wght@400;500&family=Open+Sans:wght@400;600;700&display=swap" rel="stylesheet">
<style>
  :root{
    --navy:#0b2f66;
    --teal:#006b63;
    --ink:#111;
    --page:#e4e4e4;
    --canvas:#f4f4f4;
    --white:#fff;
    --row-alt:#efefef;
    --line:#dcdcdc;
    --panel:#d2d2d2;
    --tab-dark:#161616;
  }
  *{box-sizing:border-box;margin:0;padding:0}
  html,body{width:1200px;height:706px;overflow:hidden;background:var(--page)}
  .stage{position:absolute;left:0;top:0;width:1300px;height:765px;transform:scale(.923077);transform-origin:0 0;font-family:"Montserrat",sans-serif;color:var(--ink)}
  .workspace{position:absolute;left:15px;top:15px;width:1270px;height:735px;background:var(--canvas)}

  /* top navigation */
  .topbar{position:absolute;left:15px;top:15px;width:1270px;height:60px;background:var(--white);box-shadow:0 4px 8px rgba(0,0,0,.08);display:flex}
  .brand{width:180px;display:flex;align-items:center;justify-content:center;font-weight:700;font-size:18px;letter-spacing:.3px}
  .nav-item{display:flex;align-items:center;justify-content:center;gap:10px;font-weight:700;font-size:13px;border-right:1px solid var(--line);color:var(--ink)}
  .nav-item.active{background:var(--navy);color:var(--white)}
  .horizon{width:90px}
  .spacer{width:135px;border-right:1px solid var(--line)}
  .nav-item svg{width:24px;height:24px}

  /* tabs */
  .content-shade{position:absolute;left:415px;top:170px;width:870px;height:100px;background:linear-gradient(#dedede,#f2f2f2)}
  .tab{position:absolute;background:var(--white);font-weight:600;font-size:13px;color:#333;display:flex;align-items:center;justify-content:center;border-radius:6px 6px 0 0;box-shadow:0 -1px 4px rgba(0,0,0,.06)}
  .tab.current{background:var(--tab-dark);color:var(--white)}
  .tab.small{font-size:12.5px}
  .tab-scroll{position:absolute;left:1190px;top:135px;width:40px;height:35px;background:var(--white);display:flex;align-items:center;justify-content:center}
  .tab-add{position:absolute;left:1235px;top:135px;width:40px;height:35px;background:var(--navy);border-radius:6px 6px 0 0;display:flex;align-items:center;justify-content:center}

  .export{position:absolute;left:1165px;top:212px;display:flex;align-items:center;gap:8px;font-family:"Open Sans",sans-serif;font-weight:700;font-size:17px;color:var(--navy)}

  /* data table */
  .data-card{position:absolute;left:105px;top:250px;width:1160px;background:var(--white);border-radius:8px;box-shadow:0 3px 10px rgba(0,0,0,.14);overflow:hidden}
  .data-table{border-collapse:collapse;table-layout:fixed;width:1160px;font-family:"Roboto Condensed",sans-serif;font-size:16px}
  .data-table th{height:70px;background:var(--teal);color:var(--white);font-family:"Montserrat",sans-serif;font-weight:600;font-size:16px;text-align:center;border-right:1px solid rgba(255,255,255,.25)}
  .data-table td{height:70px;padding:0 9px;border-right:1px solid #e6e6e6;line-height:1.3}
  .data-table tbody tr:nth-child(even) td{background:var(--row-alt)}
  .data-table td.model{padding-left:22px}
  .data-table td.sector{padding-left:24px}

  /* filter drawer */
  .filter-drawer{position:absolute;left:15px;top:115px;width:400px;height:230px;background:var(--panel);box-shadow:0 4px 10px rgba(0,0,0,.18)}
  .filter-handle{position:absolute;left:415px;top:135px;width:50px;height:190px;background:#c9c9c9;border-radius:0 6px 6px 0;display:flex;align-items:center;justify-content:center}
  .filter-handle span{transform:rotate(-90deg);font-weight:700;font-size:16px;letter-spacing:1px}
  .collapse-btn{position:absolute;left:452px;top:217px;width:27px;height:27px;border-radius:50%;background:var(--navy);border:2px solid var(--white);display:flex;align-items:center;justify-content:center}
  .filter-card{position:absolute;left:30px;top:130px;width:370px;height:200px;background:var(--white);border-radius:5px;overflow:hidden;font-family:"Open Sans",sans-serif}
  .filter-title{height:50px;background:var(--teal);color:var(--white);font-weight:700;font-size:17px;display:flex;align-items:center;justify-content:center}
  .filter-row{height:52px;display:flex;align-items:center;padding-left:16px;font-size:16px;border-bottom:1px solid #e8e8e8}
  .filter-row .label{width:85px}
  .filter-row b{font-weight:700;margin-right:12px}
  .filter-row .field{width:151px;height:31px;border:1px solid #cfcfcf;border-radius:5px;padding-left:13px;display:flex;align-items:center;font-size:16px}
  .filter-check{display:flex;align-items:center;gap:8px;padding:12px 0 0 14px;font-weight:600;font-size:16px}
  .filter-check i{width:18px;height:18px;border:1px solid #999;border-radius:3px;display:block}
</style>
</head>
<body>
<div class="stage">
  <div class="workspace"></div>

  <header class="topbar">
    <div class="brand">NORVEX</div>
    <div class="nav-item horizon active">250D</div>
    <div class="nav-item horizon">83D</div>
    <div class="nav-item horizon">42D</div>
    <div class="spacer"></div>
    <div class="nav-item active" style="width:140px">
      <svg viewBox="0 0 24 24" fill="none" stroke="#fff" stroke-width="2"><path d="M3 11 12 3l9 8"/><path d="M5 10v10h5v-6h4v6h5V10"/></svg>MODELS</div>
    <div class="nav-item" style="width:178px">
      <svg viewBox="0 0 24 24" fill="none" stroke="#222" stroke-width="1.6"><circle cx="12" cy="12" r="3"/><circle cx="12" cy="12" r="7" stroke-dasharray="2 2"/><circle cx="12" cy="12" r="10.5" stroke-dasharray="1.5 2.5"/></svg>SENSITIVITIES</div>
    <div class="nav-item" style="width:160px">
      <svg viewBox="0 0 24 24" fill="none" stroke="#222" stroke-width="1.8"><circle cx="7" cy="7" r="4"/><circle cx="17" cy="7" r="4"/><circle cx="7" cy="17" r="4"/><circle cx="17" cy="17" r="4"/></svg>PORTFOLIO</div>
    <div class="nav-item" style="width:152px">
      <svg viewBox="0 0 24 24" fill="none" stroke="#222" stroke-width="1.8"><rect x="2" y="3" width="20" height="18"/><path d="M5 16l4-5 3 3 4-6 3 3"/></svg>BACKTEST</div>
  </header>

  <div class="content-shade"></div>
  <div class="tab" style="left:415px;top:125px;width:128px;height:45px">PAIRS</div>
  <div class="tab current" style="left:550px;top:115px;width:155px;height:55px">ETF PAIRS</div>
  <div class="tab" style="left:712px;top:125px;width:153px;height:45px">FACTORS</div>
  <div class="tab small" style="left:870px;top:135px;width:155px;height:35px">NEW TAB TITLE #1</div>
  <div class="tab small" style="left:1030px;top:135px;width:155px;height:35px">NEW TAB TITLE #2</div>
  <div class="tab-scroll"><svg width="14" height="20" viewBox="0 0 14 20"><path d="M3 2l8 8-8 8" fill="none" stroke="#999" stroke-width="3"/></svg></div>
  <div class="tab-add"><svg width="26" height="26" viewBox="0 0 26 26" fill="none" stroke="#fff" stroke-width="2"><circle cx="13" cy="13" r="11"/><path d="M13 7v12M7 13h12"/></svg></div>

  <div class="export"><svg width="26" height="26" viewBox="0 0 26 26" fill="none" stroke="#0b2f66" stroke-width="2.4"><path d="M12 4H4v18h18v-8"/><path d="M10 16l12-12M14 4h8v8"/></svg>Export</div>

  <div class="data-card">
    <table class="data-table">
      <colgroup><col style="width:100px"><col style="width:140px"><col style="width:115px"><col style="width:85px"><col span="8" style="width:90px"></colgroup>
      <thead><tr><th>Model</th><th>Sector</th><th>Time</th><th>Quality</th><th>Stat 1</th><th>Stat 2</th><th>Stat 3</th><th>Stat 4</th><th>Stat 5</th><th>Stat 6</th><th>Stat 7</th><th>Stat 8</th></tr></thead>
      <tbody>
        <tr><td class="model">Model 1</td><td class="sector">Materials</td><td>2019-07-03<br>12:15:00.000</td><td>30.2288</td><td>2.01574</td><td>23.305</td><td>-0.149368</td><td>22.3054</td><td>4.63714</td><td>0.945706</td><td>2.81949</td><td>2.60858</td></tr>
        <tr><td class="model">Model 2</td><td class="sector">Industrials</td><td>2019-07-03<br>12:15:00.000</td><td>32.8694</td><td>0.87307</td><td>32.185</td><td>-0.033692</td><td>33.9911</td><td>11.5693</td><td>-0.472968</td><td>-0.830458</td><td>6.80646</td></tr>
        <tr><td class="model">Model 3</td><td class="sector">Consumer<br>Discretionary</td><td>2019-07-03<br>12:15:00.000</td><td>1.66002</td><td>-0.569222</td><td>159.814</td><td>0.0252328</td><td>172.616</td><td>10.2875</td><td>-0.750396</td><td>-0.385309</td><td>4.69146</td></tr>
        <tr><td class="model">Model 4</td><td class="sector">Information<br>Technology</td><td>2019-07-03<br>12:15:00.000</td><td>45.6856</td><td>0.412148</td><td>202.488</td><td>0.0084923</td><td>205.834</td><td>11.9094</td><td>-0.137913</td><td>0.449595</td><td>3.85106</td></tr>
        <tr><td class="model">Model 5</td><td class="sector">Information<br>Technology</td><td>2019-07-03<br>12:15:00.000</td><td>75.7733</td><td>7.06728</td><td>188.605</td><td>0.016913</td><td>161.665</td><td>3.82241</td><td>0.981019</td><td>1.29847</td><td>3.34927</td></tr>
      </tbody>
    </table>
  </div>

  <div class="filter-drawer"></div>
  <div class="filter-handle"><span>FILTERS</span></div>
  <div class="collapse-btn"><svg width="14" height="14" viewBox="0 0 14 14" fill="none" stroke="#fff" stroke-width="2"><path d="M12 7H2M6 3 2 7l4 4"/></svg></div>
  <div class="filter-card">
    <div class="filter-title">Filters</div>
    <div class="filter-row"><span class="label">Quality</span><b>Threshold:</b><span class="field">-10</span></div>
    <div class="filter-row"><span class="label"><b style="margin:0">Abs.</b> Stat</span><b>Threshold:</b><span class="field">-10</span></div>
    <div class="filter-check"><i></i>Apply to all tabs</div>
  </div>
</div>
</body>
</html>
```